Vellisant - Quality health delivered at your door

Vellisant offers home and Community Based Services for adults who wish to continue live independently in their communities. We increase accessibility to health care, reduce health care delivery gap, reduce mortality and morbidity, reduce health while promoting healthy living in the comfort of our patients communities or homes.

We provide on site services and deliver high quality healthcare at your door. Our experienced physicians coordinate care with our certified nurse practitioners and provide chronic care management, physical therapy, rehabilitation and medications management.

Target Market(s)

Older population living in independent living facilities

Industry/Entity Type

Health Care

Contact Information for Business Card

Vellisant

Number of Pages Required

4 page

Font styles to use
Sans Serif

Colors

Designer to choose colors to be used in the design.

```html
<!DOCTYPE html>
<html lang="en">
<head>
<meta charset="utf-8">
<title>Vellisant – Quality health delivered at your door</title>
<link href="https://fonts.googleapis.com/css2?family=Raleway:ital,wght@0,400;0,500;0,600;0,700;0,800;1,400&display=swap" rel="stylesheet">
<style>
:root{
  --orange:#f7941d;
  --green:#648a12;
  --green-dark:#1d3208;
  --ink:#1f2d0c;
  --text:#555a60;
  --white:#ffffff;
  --dot:#3b4350;
}
*{box-sizing:border-box;margin:0;padding:0}
html,body{width:1200px;height:2553px;overflow:hidden;background:var(--white)}
body{position:relative;font-family:"Raleway",sans-serif;color:var(--text)}
.abs{position:absolute}

/* header */
.top-rule{left:0;top:0;width:1200px;height:5px;background:var(--orange)}
.phone-tab{left:887px;top:0;width:236px;height:46px;background:var(--orange);clip-path:polygon(0 0,100% 0,100% 100%,8% 100%);color:var(--white);font-weight:700;font-size:16px;display:flex;align-items:center;justify-content:center;gap:12px;padding-left:18px}
.brand{left:75px;top:14px;width:160px;text-align:center}
.brand-mark{display:block;margin:0 auto;width:78px;height:78px;border-radius:50%;background:var(--green)}
.brand-name{display:block;margin-top:6px;font-size:22px;font-weight:700;color:var(--ink);letter-spacing:.5px}
.nav a{position:absolute;top:92px;font-size:13px;font-weight:700;color:var(--ink);text-decoration:none;white-space:nowrap}
.nav a.active{color:var(--green)}

/* hero */
.hero{left:0;top:141px;width:1200px;height:518px;background:linear-gradient(90deg,#eef0f8 0%,#e7e9f3 38%,#d9d5dc 55%,#c9d6ea 75%,#5f93cf 92%,#e9e4e4 100%)}
.hero-title{left:75px;top:300px;width:560px;font-size:18.5px;line-height:27px;font-weight:800;color:var(--ink);text-transform:uppercase}
.btn{display:flex;align-items:center;justify-content:center;background:var(--orange);color:var(--white);font-weight:700;font-size:13.5px;text-transform:uppercase;letter-spacing:.5px}
.hero-btn{left:75px;top:400px;width:179px;height:44px}
.dots span{position:absolute;width:12px;height:12px;background:var(--dot)}
.dots span.on{background:var(--green)}

/* section heads */
.section-title{left:0;width:1200px;text-align:center;font-size:26px;font-weight:800;color:var(--ink);text-transform:uppercase;letter-spacing:.5px}
.rule{height:3px;width:68px;background:var(--orange)}

.welcome-text{left:70px;top:780px;width:1060px;text-align:center;font-size:14.5px;line-height:23px}

/* services */
.services{left:0;top:906px;width:1200px;height:457px;background:var(--green)}
.services .section-title{color:var(--white)}
.services-intro{left:0;top:1030px;width:1200px;text-align:center;font-size:14.5px;color:var(--white)}
.service{width:260px;text-align:center}
.service-icon{display:flex;align-items:center;justify-content:center;margin:0 auto;width:92px;height:92px;border-radius:50%;background:var(--orange);border:3px solid var(--white)}
.service-label{margin-top:14px;font-size:18px;font-weight:600;color:var(--white)}
.services-btn{left:495px;top:1273px;width:210px;height:46px}

/* testimonial */
.testimonial{left:0;top:1363px;width:1200px;height:368px;background:linear-gradient(90deg,#e7e3e8 0%,#e6e2e7 45%,#d6dee6 62%,#b9d8e6 80%,#e9d2d2 100%)}
.testimonial-title{left:75px;top:1412px;font-size:26px;font-weight:800;color:var(--ink);text-transform:uppercase}
.quote-badge{left:75px;top:1497px;width:40px;height:40px;border-radius:50%;background:var(--green)}
.quote-text{left:138px;top:1492px;width:480px;font-size:14.5px;line-height:27px;font-style:italic;color:var(--text)}
.quote-name{left:138px;top:1609px;font-size:11.5px;font-weight:700;color:var(--orange);text-transform:uppercase}
.t-dots span{position:absolute;top:1671px;width:10px;height:10px;border-radius:50%;background:#9aa0a8}
.t-dots span.on{background:var(--ink)}

/* blog */
.post{top:1859px;width:330px}
.post-photo{width:330px;height:204px}
.post-title{margin-top:22px;font-size:17px;font-weight:800;color:var(--ink);text-transform:uppercase}
.post-text{margin-top:6px;font-size:14.5px;line-height:22px;color:var(--text)}
.post-link{display:block;margin-top:12px;font-size:11px;font-weight:700;color:var(--orange);text-transform:uppercase}

/* footer */
.footer{left:0;top:2281px;width:1200px;height:272px;background:var(--green-dark)}
.foot-brand{left:500px;top:2252px;width:200px;text-align:center}
.foot-mark{display:block;margin:0 auto;width:70px;height:70px;border-radius:50%;background:var(--orange)}
.foot-name{display:block;margin-top:6px;font-size:22px;font-weight:700;color:var(--white)}
.copyright{left:450px;top:2380px;width:300px;text-align:center;font-size:11.5px;line-height:20px;color:#d9dccf}
.foot-head{font-size:12px;font-weight:800;color:var(--orange);text-transform:uppercase;margin-bottom:10px}
.foot-col{top:2330px;font-size:12px;color:#e3e6da}
.foot-list li{list-style:none;height:26px}
.contact-row{display:flex;align-items:center;gap:16px;height:30px}
.news-input{width:191px;height:34px;background:var(--white);border:1px solid #ccc;font-size:11px;color:#666;padding:10px 12px;margin-top:12px}
.news-btn{margin-left:116px;margin-top:10px;width:75px;height:30px;background:var(--green);color:var(--white);font-size:11.5px;font-weight:800;display:flex;align-items:center;justify-content:center}
.social li{list-style:none;display:flex;align-items:center;gap:12px;height:32px}
.social i{display:block;width:11px;height:11px;background:#e3e6da}
</style>
</head>
<body>

<div class="abs top-rule"></div>
<div class="abs phone-tab">
  <svg width="14" height="14" viewBox="0 0 24 24"><path fill="#fff" d="M6.6 10.8a15.1 15.1 0 0 0 6.6 6.6l2.2-2.2c.3-.3.7-.4 1-.2 1.1.4 2.3.6 3.6.6.6 0 1 .4 1 1V20c0 .6-.4 1-1 1C10.6 21 3 13.4 3 4c0-.6.4-1 1-1h3.5c.6 0 1 .4 1 1 0 1.2.2 2.4.6 3.6.1.3 0 .7-.2 1z"/></svg>
  <span>1-800-555-0142</span>
</div>

<div class="abs brand"><span class="brand-mark"></span><span class="brand-name">VELLISANT</span></div>

<nav class="nav">
  <a class="active" style="left:521px">HOME</a>
  <a style="left:604px">ABOUT US</a>
  <a style="left:717px">SERVICES</a>
  <a style="left:824px">BLOG</a>
  <a style="left:906px">LATEST NEWS</a>
  <a style="left:1043px">CONTACT US</a>
</nav>

<div class="abs hero" role="img" aria-label="Photo of a smiling nurse caring for an elderly woman with a cane at home"></div>
<h1 class="abs hero-title">Vellisant offers home and community based services for adults who wish to continue live independently in their communities</h1>
<div class="abs btn hero-btn">Read More</div>
<div class="dots"><span class="on" style="left:75px;top:476px"></span><span style="left:94px;top:476px"></span><span style="left:112px;top:476px"></span><span style="left:131px;top:476px"></span></div>

<h2 class="abs section-title" style="top:700px">Welcome to our website</h2>
<div class="abs rule" style="left:566px;top:751px"></div>
<p class="abs welcome-text">Vellisant offers home and Community Based Services for adults who wish to continue to live independently in the comfort of their communities. We provide on site services and deliver high quality healthcare at your door. Our experienced physicians coordinate care with our certified nurse practitioners and provide chronic care management, physical therapy, rehabilitation and medications management.</p>

<section class="abs services"></section>
<h2 class="abs section-title" style="top:955px;color:var(--white)">Our Services</h2>
<div class="abs rule" style="left:566px;top:999px"></div>
<p class="abs services-intro">Vellisant offers home and Community Based Services for adults who wish to continue live independently in their communities.</p>

<div class="abs service" style="left:66px;top:1082px">
  <div class="service-icon"><svg width="40" height="40" viewBox="0 0 40 40" fill="none" stroke="#fff" stroke-width="3"><circle cx="20" cy="13" r="7"/><path d="M7 36c0-8 6-13 13-13s13 5 13 13"/><path d="M20 27v6M17 30h6"/></svg></div>
  <div class="service-label">Home Health Assistance</div>
</div>
<div class="abs service" style="left:333px;top:1082px">
  <div class="service-icon"><svg width="42" height="40" viewBox="0 0 42 40" fill="none" stroke="#fff" stroke-width="3"><circle cx="21" cy="9" r="5"/><path d="M6 30h30M10 30l6-10h12l4 10"/><path d="M6 34h30"/></svg></div>
  <div class="service-label">Physical Therapy</div>
</div>
<div class="abs service" style="left:605px;top:1082px">
  <div class="service-icon"><svg width="40" height="40" viewBox="0 0 40 40" fill="none" stroke="#fff" stroke-width="3"><path d="M12 36v-8c-4-3-5-7-5-11C7 9 13 4 21 4s13 6 13 13c0 3-2 5-3 6v5h-5v8"/><circle cx="20" cy="16" r="4"/></svg></div>
  <div class="service-label">Mental Health</div>
</div>
<div class="abs service" style="left:876px;top:1082px">
  <div class="service-icon"><svg width="40" height="40" viewBox="0 0 40 40"><path fill="#fff" d="M10 8c4-3 7 0 10 0s6-3 10 0c3 3 2 9 0 13-1 3-1 6-2 10-1 4-4 4-5 0l-2-7c-1-2-1-2-2 0l-2 7c-1 4-4 4-5 0-1-4-1-7-2-10-2-4-3-10 0-13z"/></svg></div>
  <div class="service-label">Dental Health</div>
</div>

<div class="abs btn services-btn">View All Services</div>

<section class="abs testimonial" role="img" aria-label="Photo of a smiling elderly couple embracing"></section>
<h2 class="abs testimonial-title">What our client says</h2>
<div class="abs rule" style="left:75px;top:1462px"></div>
<div class="abs quote-badge"><svg width="40" height="40" viewBox="0 0 40 40"><path fill="#fff" d="M12 15h6v6l-3 6h-3l2-5h-2zM22 15h6v6l-3 6h-3l2-5h-2z"/></svg></div>
<p class="abs quote-text">Lorem ipsum dolor sit amet, consect- etuer adipiscing elit, sed diam nonummy nibh euismod tincidunt ut laoreet dolore magna aliquam erat volutpat. Ut wisi enim ad minim veniam, quis nostrud exerci tation ullam..."</p>
<p class="abs quote-name">-Name Heading</p>
<div class="t-dots"><span class="on" style="left:75px"></span><span style="left:92px"></span><span style="left:110px"></span><span style="left:127px"></span></div>

<h2 class="abs section-title" style="top:1772px">Blog Posts</h2>
<div class="abs rule" style="left:566px;top:1825px"></div>

<article class="abs post" style="left:75px">
  <div class="post-photo" role="img" aria-label="Photo of a carer helping an elderly man sit up in bed" style="background:linear-gradient(120deg,#d9c7b4,#b99a84 50%,#e8e0d8)"></div>
  <h3 class="post-title">Lorem ipsum dolor sit amet</h3>
  <p class="post-text">Etuer adipiscing elit, sed diam nonummy nibh euismod tincidunt ut laoreet dolore magna aliquam erat volutpat...</p>
  <span class="post-link">Continue Reading</span>
</article>
<article class="abs post" style="left:436px">
  <div class="post-photo" role="img" aria-label="Photo of a therapist guiding an older man through walking exercise" style="background:linear-gradient(120deg,#e4e7ea,#c9ccd0 50%,#9fb3c4)"></div>
  <h3 class="post-title">Lorem ipsum dolor sit amet</h3>
  <p class="post-text">Etuer adipiscing elit, sed diam nonummy nibh euismod tincidunt ut laoreet dolore magna aliquam erat volutpat...</p>
  <span class="post-link">Continue Reading</span>
</article>
<article class="abs post" style="left:797px">
  <div class="post-photo" role="img" aria-label="Photo of a nurse assisting an elderly man on an exercise bike in a rehab gym" style="background:linear-gradient(120deg,#7fa3b8,#c9a27a 50%,#d9cdb9)"></div>
  <h3 class="post-title">Lorem ipsum dolor sit amet</h3>
  <p class="post-text">Etuer adipiscing elit, sed diam nonummy nibh euismod tincidunt ut laoreet dolore magna aliquam erat volutpat...</p>
  <span class="post-link">Continue Reading</span>
</article>

<footer class="abs footer"></footer>
<div class="abs foot-brand"><span class="foot-mark"></span><span class="foot-name">VELLISANT</span></div>
<p class="abs copyright">Copyright © 2017, Company Name<br>All Right Reserved</p>

<div class="abs foot-col" style="left:75px">
  <div class="foot-head">Site Map</div>
  <ul class="foot-list"><li>Home</li><li>About Us</li><li>Services</li><li>Blog</li><li>Latest News</li><li>Contact Us</li></ul>
</div>

<div class="abs foot-col" style="left:269px">
  <div class="foot-head">Contact Info</div>
  <p style="line-height:21px;margin-bottom:6px">4120 Alder Lane,<br>Riverton, RT5 2KL</p>
  <div class="contact-row"><svg width="14" height="14" viewBox="0 0 24 24"><path fill="#e3e6da" d="M6.6 10.8a15.1 15.1 0 0 0 6.6 6.6l2.2-2.2c.3-.3.7-.4 1-.2 1.1.4 2.3.6 3.6.6.6 0 1 .4 1 1V20c0 .6-.4 1-1 1C10.6 21 3 13.4 3 4c0-.6.4-1 1-1h3.5c.6 0 1 .4 1 1 0 1.2.2 2.4.6 3.6.1.3 0 .7-.2 1z"/></svg><span>1-800-555-0142</span></div>
  <div class="contact-row"><svg width="14" height="12" viewBox="0 0 24 18"><path fill="#e3e6da" d="M0 0h24v2L12 10 0 2zM0 5l12 8 12-8v13H0z"/></svg><span>hello@vellisant.com</span></div>
  <div class="contact-row"><svg width="14" height="12" viewBox="0 0 24 18"><path fill="#e3e6da" d="M0 0h24v2L12 10 0 2zM0 5l12 8 12-8v13H0z"/></svg><span>Map Direction</span></div>
</div>

<div class="abs foot-col" style="left:754px;width:200px">
  <div class="foot-head">Enail Newsletter</div>
  <p style="line-height:21px">Consectetuer adipiscing elit, sed diam nonummy nibh...</p>
  <div class="news-input">Enter Email Address</div>
  <div class="news-btn">SIGN UP</div>
</div>

<div class="abs foot-col" style="left:1004px">
  <div class="foot-head">Connect Us</div>
  <ul class="social">
    <li><i></i>Circlebook</li>
    <li><i></i>Chirper</li>
    <li><i></i>Worknet</li>
    <li><i></i>Orbit +</li>
    <li><i></i>ViewTube</li>
  </ul>
</div>

</body>
</html>
```